Home Remodeling company needs a business card design

we need a business card design for home remodeling company in hamilton county, indiana USA. we offers a wide range of construction services including whole house renovations, Design and Build Basements and Kitchen and Bathroom Remodeling . we would like to see designs for both site of business card that use the same color of the company logo and also including all information below :
1- Karim Feltous CEO / General Contractor
2- all company contacts Telephone numbers ( 1-888-DULOM-47 ) ( 317-555-0193) email address ( info@dulomhome.com) website ( www.dulomhome.com ) and social media logos (Facebook- twitter- google plus )
3- company logo
4- licensed . insured . bonded

```html
<!DOCTYPE html>
<html lang="en">
<head>
<meta charset="utf-8">
<title>Dulom Home Remodeling – Business Card</title>
<link rel="stylesheet" href="https://fonts.googleapis.com/css2?family=Cabin:wght@400;500;600;700&display=swap">
<style>
  :root {
    --backdrop: #8e8f90;
    --card-light: #e9e9eb;
    --card-dark: #353537;
    --brand-red: #a92a33;
    --ink: #343436;
    --text-light: #f2f2f2;
    --text-soft: #dcdcdc;
    --mark-light: #e6e6e8;
  }
  * { margin: 0; padding: 0; box-sizing: border-box; }
  html, body {
    width: 1105px;
    height: 1200px;
    overflow: hidden;
    background: var(--backdrop);
    font-family: "Cabin", sans-serif;
  }
  .card {
    position: absolute;
    left: 182px;
    width: 746px;
    height: 426px;
    overflow: hidden;
  }
  .card-front { top: 119px; background: var(--card-dark); }
  .card-back { top: 637px; background: var(--brand-red); }

  /* front: brand side */
  .brand-panel {
    position: absolute;
    left: 0; top: 0;
    width: 388px; height: 100%;
    background: var(--card-light);
  }
  .brand-pointer {
    position: absolute;
    left: 387px; top: 79px;
    width: 41px; height: 52px;
  }
  .brand-lockup {
    position: absolute;
    left: 50px; top: 180px;
    display: flex;
    align-items: center;
    gap: 12px;
  }
  .brand-square {
    width: 12px; height: 12px;
    background: var(--brand-red);
  }
  .brand-name {
    font-size: 50px;
    font-weight: 700;
    letter-spacing: 2px;
    color: var(--ink);
    line-height: 1;
  }

  /* front: contact side */
  .pointer-square {
    position: absolute;
    left: 385px; top: 96px;
    width: 11px; height: 11px;
    background: var(--brand-red);
  }
  .person {
    position: absolute;
    left: 443px; top: 74px;
    color: var(--text-light);
  }
  .person-name {
    font-size: 27px;
    font-weight: 600;
    letter-spacing: 0.3px;
    line-height: 1.1;
  }
  .person-title {
    font-size: 20px;
    font-weight: 400;
    color: var(--text-soft);
    margin-top: 4px;
  }
  .contact-list {
    position: absolute;
    left: 448px; top: 236px;
    list-style: none;
  }
  .contact-item {
    display: flex;
    align-items: center;
    height: 29px;
    font-size: 20px;
    color: var(--text-light);
  }
  .contact-icon {
    width: 18px; height: 18px;
    margin-right: 13px;
    fill: var(--text-light);
  }

  /* back */
  .back-mark {
    position: absolute;
    left: 0; right: 0; top: 120px;
    display: flex;
    justify-content: center;
    align-items: center;
    gap: 18px;
  }
  .back-mark-square {
    width: 22px; height: 22px;
    background: var(--mark-light);
  }
  .back-mark-name {
    font-size: 88px;
    font-weight: 700;
    letter-spacing: 4px;
    color: var(--mark-light);
    line-height: 1;
  }
  .credentials {
    position: absolute;
    left: 0; right: 0; top: 318px;
    text-align: center;
    font-size: 21px;
    color: var(--text-light);
    letter-spacing: 0.3px;
  }
  .social-row {
    position: absolute;
    left: 0; right: 0; top: 360px;
    display: flex;
    justify-content: center;
    align-items: center;
    gap: 6px;
  }
  .social-rule {
    width: 70px; height: 1px;
    background: rgba(255,255,255,0.55);
  }
  .social-dot {
    width: 26px; height: 26px;
    border-radius: 50%;
    background: var(--mark-light);
  }
  .social-rule:first-child { margin-right: 4px; }
  .social-rule:last-child { margin-left: 4px; }
</style>
</head>
<body>

<section class="card card-front">
  <div class="brand-panel">
    <div class="brand-lockup">
      <span class="brand-square"></span>
      <span class="brand-name">DULOM</span>
    </div>
  </div>
  <svg class="brand-pointer" viewBox="0 0 41 52" aria-hidden="true">
    <polygon points="0,0 41,26 0,52" fill="var(--card-light)"/>
  </svg>
  <span class="pointer-square"></span>

  <div class="person">
    <p class="person-name">Karim Feltous</p>
    <p class="person-title">CEO / General Contractor</p>
  </div>

  <ul class="contact-list">
    <li class="contact-item">
      <svg class="contact-icon" viewBox="0 0 24 24" aria-hidden="true"><path d="M6.6 10.8a15.1 15.1 0 0 0 6.6 6.6l2.2-2.2c.3-.3.7-.4 1-.2 1.1.4 2.3.6 3.6.6.6 0 1 .4 1 1V20c0 .6-.4 1-1 1C10.6 21 3 13.4 3 4c0-.6.4-1 1-1h3.5c.6 0 1 .4 1 1 0 1.3.2 2.5.6 3.6.1.3 0 .7-.2 1z"/></svg>
      <span>1-888-DULOM-47</span>
    </li>
    <li class="contact-item">
      <svg class="contact-icon" viewBox="0 0 24 24" aria-hidden="true"><path d="M7 1h10a2 2 0 0 1 2 2v18a2 2 0 0 1-2 2H7a2 2 0 0 1-2-2V3a2 2 0 0 1 2-2zm0 3v14h10V4zm5 15.2a1.1 1.1 0 1 0 0 2.2 1.1 1.1 0 0 0 0-2.2z"/></svg>
      <span>317-555-0193</span>
    </li>
    <li class="contact-item">
      <svg class="contact-icon" viewBox="0 0 24 24" aria-hidden="true"><path d="M2 5h20v14H2zm2 2v.4l8 5.2 8-5.2V7zm0 2.8V17h16V9.8l-8 5.2z"/></svg>
      <span>info@dulomhome.com</span>
    </li>
    <li class="contact-item">
      <svg class="contact-icon" viewBox="0 0 24 24" aria-hidden="true"><path d="M12 2a10 10 0 1 0 0 20 10 10 0 0 0 0-20zm-1 17.9A8 8 0 0 1 4.2 10.2L9 15v1a2 2 0 0 0 2 2zm6.9-2.5A2 2 0 0 0 16 16h-1v-3a1 1 0 0 0-1-1H8v-2h2a1 1 0 0 0 1-1V7h2a2 2 0 0 0 2-2v-.4a8 8 0 0 1 2.9 12.8z"/></svg>
      <span>www.dulomhome.com</span>
    </li>
  </ul>
</section>

<section class="card card-back">
  <div class="back-mark">
    <span class="back-mark-square"></span>
    <span class="back-mark-name">DULOM</span>
  </div>
  <p class="credentials">LICENSED | INSURED | BONDED</p>
  <div class="social-row" role="img" aria-label="Social media links">
    <span class="social-rule"></span>
    <span class="social-dot"></span>
    <span class="social-dot"></span>
    <span class="social-dot"></span>
    <span class="social-rule"></span>
  </div>
</section>

</body>
</html>
```